Recipe Card Design

I have a small kitchen store in Livingston Montana, and I would like to have recipe cards (4x6 postcard) designed with my logo, lines for recipe writing, all in black and white. My website is here: www.brambleforkcookware.com

Store

```html
<!DOCTYPE html>
<html lang="en">
<head>
<meta charset="utf-8">
<title>Bramblefork Cookware – Recipe Card</title>
<link href="https://fonts.googleapis.com/css2?family=Zilla+Slab:wght@700&family=Roboto:wght@400&display=swap" rel="stylesheet">
<style>
  :root {
    --ink: #000000;
    --paper: #ffffff;
    --fade-mid: #7a7a7a;
  }
  html, body {
    margin: 0;
    padding: 0;
    overflow: hidden;
    background: var(--paper);
  }
  .recipe-card {
    position: relative;
    width: 1200px;
    height: 929px;
    background: var(--paper);
    overflow: hidden;
    font-family: "Zilla Slab", Georgia, serif;
    color: var(--ink);
  }
  .brand-artwork {
    position: absolute;
    left: 54px;
    top: 54px;
    width: 642px;
    height: 752px;
    background: linear-gradient(90deg, var(--ink) 0%, var(--ink) 30%, var(--fade-mid) 58%, var(--paper) 100%);
  }
  .brand-name {
    position: absolute;
    left: 54px;
    top: 820px;
    margin: 0;
    font-size: 26px;
    line-height: 1;
    font-weight: 700;
    letter-spacing: 0.12em;
    text-transform: uppercase;
    color: var(--ink);
    white-space: nowrap;
  }
  .writing-lines {
    position: absolute;
    left: 0;
    top: 0;
    width: 1200px;
    height: 929px;
  }
  .writing-lines line {
    stroke: var(--ink);
    stroke-width: 3.5;
  }
  .field-label {
    position: absolute;
    margin: 0;
    font-weight: 700;
    text-transform: uppercase;
    line-height: 1;
    color: var(--ink);
    white-space: nowrap;
  }
  .field-label--recipe {
    left: 498px;
    top: 66px;
    font-size: 50px;
    letter-spacing: 0.01em;
  }
  .field-label--ingredients {
    left: 504px;
    top: 204px;
    font-size: 25px;
  }
  .field-label--instructions {
    left: 518px;
    top: 366px;
    font-size: 25px;
  }
  .web-address {
    position: absolute;
    right: 36px;
    top: 878px;
    margin: 0;
    font-family: "Roboto", Arial, sans-serif;
    font-size: 17px;
    color: var(--ink);
  }
</style>
</head>
<body>
  <main class="recipe-card">
    <div class="brand-artwork" role="img" aria-label="Black and white illustration of a chef in a cowboy hat and apron cooking at a stove"></div>
    <p class="brand-name">Bramblefork Cookware</p>

    <svg class="writing-lines" viewBox="0 0 1200 929" aria-hidden="true">
      <line x1="714" y1="110" x2="1116" y2="110"/>
      <line x1="504" y1="166" x2="1116" y2="166"/>
      <line x1="714" y1="224" x2="1116" y2="224"/>
      <line x1="504" y1="278" x2="1116" y2="278"/>
      <line x1="504" y1="334" x2="1116" y2="334"/>
      <line x1="714" y1="390" x2="1116" y2="390"/>
      <line x1="534" y1="446" x2="1116" y2="446"/>
      <line x1="534" y1="502" x2="1116" y2="502"/>
      <line x1="534" y1="558" x2="1116" y2="558"/>
      <line x1="534" y1="614" x2="1116" y2="614"/>
      <line x1="534" y1="670" x2="1116" y2="670"/>
      <line x1="534" y1="726" x2="1116" y2="726"/>
      <line x1="534" y1="782" x2="1116" y2="782"/>
      <line x1="534" y1="838" x2="1116" y2="838"/>
    </svg>

    <h1 class="field-label field-label--recipe">Recipe</h1>
    <h2 class="field-label field-label--ingredients">Ingredients</h2>
    <h2 class="field-label field-label--instructions">Instructions</h2>

    <p class="web-address">www.brambleforkcookware.com</p>
  </main>
</body>
</html>
```